Business card design for Automotive workshop

We need a business card for a new automotive repair and tyre shop called Keelstone Prime Automotive located in New Zealand. We are a clean, modern and fresh workshop and company.

Front needs to feature logo,
my name:
Marlo Fenwicke (director)

Address:
48 Tarn Lane
Harrowdene 3592

Phone: 07 594 2713
Mobile: 027 451 9362
Email: office@keelstoneautomotive.example.nz
Website: keelstoneautomotive.example.nz

Back needs to feature an area to write down appointment details, date and time.

Also feature a list of jobs and work we do such as,
Vehicle Servicing
All Mechanical Repairs
Warrant of Fitness
Tyres & Wheel Alignments
Automotive Diagnostics
Automotive Parts & Supplies

```html
<!DOCTYPE html>
<html lang="en">
<head>
<meta charset="utf-8">
<title>Keelstone Prime Automotive – Business Card</title>
<link rel="stylesheet" href="https://fonts.googleapis.com/css2?family=Open+Sans:wght@400&family=Raleway:wght@700&family=Roboto:wght@400;500&display=swap">
<style>
  :root {
    --backdrop: #2e2e2e;
    --card-front: #eeeeee;
    --card-back-top: #f4f2f2;
    --brand-red: #e31e24;
    --ink: #1c1c1c;
    --rule: #b5b5b5;
    --white: #ffffff;
  }
  * { margin: 0; padding: 0; box-sizing: border-box; }
  html, body { width: 1200px; height: 1200px; overflow: hidden; }
  body { background: var(--backdrop); position: relative; font-family: "Roboto", Arial, sans-serif; }

  .card {
    position: absolute;
    top: 310px;
    height: 593px;
    overflow: hidden;
    text-align: center;
    box-shadow: 0 4px 12px rgba(0,0,0,.45);
  }
  .card-front { left: 234px; width: 364px; background: var(--card-front); }
  .card-back { left: 627px; width: 369px; background: var(--card-back-top); }

  /* Front */
  .wordmark {
    position: absolute; top: 150px; left: 0; right: 0;
    font-family: "Raleway", Arial, sans-serif; font-weight: 700;
    color: var(--brand-red); line-height: 1.05;
    letter-spacing: 1px;
  }
  .wordmark .main { display: block; font-size: 31px; }
  .wordmark .sub { display: block; font-size: 15px; letter-spacing: 5px; margin-top: 4px; }

  .person { position: absolute; top: 312px; left: 0; right: 0; }
  .person-name {
    font-family: "Raleway", Arial, sans-serif; font-weight: 700;
    font-size: 24px; color: var(--brand-red); line-height: 1;
  }
  .person-role { font-size: 17px; color: var(--ink); margin-top: 3px; }

  .icon-row {
    position: absolute; top: 376px; left: 86px; width: 193px; height: 20px;
    display: flex; align-items: center; justify-content: center; gap: 3px;
  }
  .icon-row::before, .icon-row::after {
    content: ""; flex: 1; height: 1px; background: var(--rule);
  }
  .icon-row::before { margin-right: 5px; }
  .icon-row::after { margin-left: 5px; }
  .icon { width: 20px; height: 20px; display: block; }

  .contact {
    position: absolute; top: 412px; left: 0; right: 0;
    font-size: 17px; line-height: 21.5px; color: var(--ink);
    list-style: none;
  }
  .divider {
    position: absolute; top: 512px; left: 86px; width: 193px; height: 1px; background: var(--rule);
  }
  .address {
    position: absolute; top: 526px; left: 0; right: 0;
    font-size: 17px; color: var(--ink); font-style: normal;
  }
  .front-band {
    position: absolute; left: 0; right: 0; bottom: 0; height: 16px; background: var(--brand-red);
  }

  /* Back */
  .appointment { position: absolute; top: 0; left: 0; right: 0; height: 304px; }
  .appointment h2 {
    position: absolute; top: 106px; left: 0; right: 0;
    font-weight: 500; font-size: 26px; color: var(--brand-red); letter-spacing: .2px;
  }
  .field {
    position: absolute; left: 72px; width: 225px;
    display: flex; align-items: center; font-size: 20px; color: var(--ink);
  }
  .field .label { width: 67px; text-align: left; }
  .field .line { flex: 1; height: 1px; background: #c9c9c9; margin-top: 4px; }
  .field-date { top: 177px; }
  .field-time { top: 231px; }

  .services {
    position: absolute; top: 304px; left: 0; right: 0; bottom: 0;
    background: var(--brand-red); color: var(--white);
  }
  .services h2 {
    margin-top: 56px; font-weight: 500; font-size: 23px;
  }
  .services ul {
    list-style: none; margin-top: 11px;
    font-family: "Open Sans", Arial, sans-serif; font-size: 15px; line-height: 27.2px;
  }
</style>
</head>
<body>

<section class="card card-front" aria-label="Business card front">
  <div class="wordmark">
    <span class="main">KEELSTONE PRIME</span>
    <span class="sub">AUTOMOTIVE</span>
  </div>

  <div class="person">
    <h1 class="person-name">MARLO FENWICKE</h1>
    <p class="person-role">Director</p>
  </div>

  <div class="icon-row" aria-hidden="true">
    <svg class="icon" viewBox="0 0 20 20"><rect width="20" height="20" rx="4" fill="#e31e24"/><path d="M4.5 9.5h11l-1.5-3h-8z M6 10h8v4H6z" fill="#fff"/><circle cx="10" cy="12" r="1.2" fill="#e31e24"/></svg>
    <svg class="icon" viewBox="0 0 20 20"><rect width="20" height="20" rx="4" fill="#e31e24"/><rect x="6.5" y="3.5" width="7" height="13" rx="1.2" fill="none" stroke="#fff" stroke-width="1.4"/><circle cx="10" cy="14.2" r=".8" fill="#fff"/></svg>
    <svg class="icon" viewBox="0 0 20 20"><rect width="20" height="20" rx="4" fill="#e31e24"/><rect x="4" y="6" width="12" height="8.5" fill="none" stroke="#fff" stroke-width="1.4"/><path d="M4 6l6 5 6-5" fill="none" stroke="#fff" stroke-width="1.4"/></svg>
    <svg class="icon" viewBox="0 0 20 20"><rect width="20" height="20" rx="4" fill="#e31e24"/><circle cx="10" cy="10" r="6" fill="none" stroke="#fff" stroke-width="1.4"/><path d="M4 10h12M10 4c-3 3-3 9 0 12M10 4c3 3 3 9 0 12" fill="none" stroke="#fff" stroke-width="1.1"/></svg>
  </div>

  <ul class="contact">
    <li>07 594 2713</li>
    <li>027 451 9362</li>
    <li>office@keelstoneautomotive.example.nz</li>
    <li>keelstoneautomotive.example.nz</li>
  </ul>

  <div class="divider"></div>
  <address class="address">48 Tarn Lane, Harrowdene 3592</address>
  <div class="front-band"></div>
</section>

<section class="card card-back" aria-label="Business card back">
  <div class="appointment">
    <h2>NEXT APPOINTMENT</h2>
    <div class="field field-date"><span class="label">DATE</span><span class="line"></span></div>
    <div class="field field-time"><span class="label">TIME</span><span class="line"></span></div>
  </div>

  <div class="services">
    <h2>WORK WE DO</h2>
    <ul>
      <li>Vehicle Servicing</li>
      <li>All Mechanical Repairs</li>
      <li>Warrant of Fitness</li>
      <li>Tyres &amp; Wheel Alignments</li>
      <li>Automotive Diagnostics</li>
      <li>Automotive Parts &amp; Supplies</li>
    </ul>
  </div>
</section>

</body>
</html>
```